Tovel & Associates - London New Letting and Property Management Company *

Tovel & Associates LTD is a new company based in London, and works with brand new residential property in the city centre.

We are aiming to have 1000 new properties a year.

We are looking for something modern and minimalistic :
Logo ,Monogram, Paper Head and Business Card.

Target Market(s)

Internation landlords

Industry/Entity Type

Real Estate

Logo Text

Tovel & Associates

Colors

Designer to choose colors to be used in the design.

Requirements
Nice to have
• A particular monogram with "TA"
Should not have
• Little House over the logo

```html
<!DOCTYPE html>
<html lang="en">
<head>
<meta charset="utf-8">
<title>Tovel &amp; Associates – Business Card</title>
<link href="https://fonts.googleapis.com/css2?family=Work+Sans:wght@400;500;600&display=swap" rel="stylesheet">
<style>
  :root {
    --bg: #1e1e1e;
    --card-dark: #1b1c1d;
    --card-light: #f3f3f3;
    --navy: #1f5276;
    --sky: #27a9e8;
    --grey: #6b6b6b;
  }
  * { margin: 0; padding: 0; box-sizing: border-box; }
  html, body {
    width: 1200px; height: 900px; overflow: hidden;
    background: var(--bg);
    font-family: "Work Sans", Arial, sans-serif;
  }
  .stage {
    width: 1200px; height: 900px;
    display: flex; flex-direction: column; align-items: center; justify-content: center;
    gap: 40px;
  }
  .card {
    position: relative;
    width: 660px; height: 377px;
    overflow: hidden;
    box-shadow: 0 18px 40px rgba(0,0,0,.55);
  }
  .card--front {
    background: linear-gradient(135deg, #19191a 0%, #1d1e1f 60%, #2a2a2a 100%);
    display: flex; align-items: center; justify-content: center;
  }
  .brand {
    display: flex; align-items: center; gap: 12px;
    color: var(--navy);
    font-weight: 600;
    text-transform: uppercase;
    letter-spacing: 2px;
  }
  .brand__square { width: 16px; height: 16px; background: currentColor; }
  .card--front .brand { font-size: 26px; color: #266a98; }
  .card--back { background: var(--card-light); }
  .card--back .brand {
    position: absolute; right: 50px; top: 70px; font-size: 18px;
  }
  .holder { position: absolute; left: 40px; top: 84px; }
  .holder__name {
    color: var(--navy); font-size: 30px; font-weight: 500;
    text-transform: uppercase; letter-spacing: 1px; line-height: 1;
  }
  .holder__role { color: var(--grey); font-size: 17px; margin-top: 6px; }
  .divider {
    position: absolute; left: 40px; right: 50px; top: 158px;
    border-top: 2px solid var(--navy);
  }
  .contacts {
    position: absolute; left: 40px; top: 178px;
    list-style: none; color: var(--grey); font-size: 17px; line-height: 29px;
  }
  .contacts li { display: flex; align-items: center; gap: 10px; }
  .contacts svg { width: 12px; height: 12px; flex: none; }
  .contacts .web strong { color: var(--navy); font-weight: 500; }
  .address {
    position: absolute; right: 50px; top: 262px;
    color: var(--grey); font-size: 18px; line-height: 26px; text-align: left;
    letter-spacing: .5px;
  }
  .bands { position: absolute; left: 0; bottom: 0; width: 660px; height: 377px; }
</style>
</head>
<body>
<main class="stage">
  <section class="card card--front" aria-label="Card front">
    <div class="brand"><span class="brand__square"></span>Tovel &amp; Associates</div>
  </section>

  <section class="card card--back" aria-label="Card back">
    <div class="holder">
      <h1 class="holder__name">Dorian Hale</h1>
      <p class="holder__role">Director</p>
    </div>
    <div class="brand"><span class="brand__square"></span>Tovel &amp; Associates</div>
    <div class="divider"></div>
    <ul class="contacts">
      <li>
        <svg viewBox="0 0 12 12"><path d="M2.5 1 L4.5 1 L5 3.5 L3.8 4.4 Q5 7 7.6 8.2 L8.5 7 L11 7.5 L11 9.5 Q10.5 11 9 11 Q1 10 1 3 Q1 1.5 2.5 1Z" fill="#1f5276"/></svg>
        +44 20 7946 0321
      </li>
      <li>
        <svg viewBox="0 0 12 12"><rect x="1" y="2.5" width="10" height="7" fill="none" stroke="#1f5276" stroke-width="1.3"/><path d="M1 2.5 L6 6.5 L11 2.5" fill="none" stroke="#1f5276" stroke-width="1.3"/></svg>
        info@tovelassociates.com
      </li>
      <li class="web">
        <svg viewBox="0 0 12 12"><circle cx="6" cy="6" r="5" fill="none" stroke="#1f5276" stroke-width="1.1"/><ellipse cx="6" cy="6" rx="2.2" ry="5" fill="none" stroke="#1f5276" stroke-width="1"/><path d="M1 6 H11 M2 3.5 H10 M2 8.5 H10" stroke="#1f5276" stroke-width=".9"/></svg>
        <span>www.<strong>tovelassociates</strong>.com</span>
      </li>
    </ul>
    <p class="address">14 Harlow Crescent<br>London W2 4RT</p>
    <svg class="bands" viewBox="0 0 660 377" aria-hidden="true">
      <path d="M0 337 L330 352 Q340 353 345 356 L0 346 Z" fill="#27a9e8"/>
      <path d="M0 351 L330 362 C350 362 355 347 385 347 L660 338 L660 377 L0 377 Z" fill="#1f5276"/>
    </svg>
  </section>
</main>
</body>
</html>
```